Eyecatching website design for commercial lighting business

This contest is all about the graphic design aspect. We need a striking website design for a commercial lighting company. We want something really eye catching to introduce people to our range of induction and LED lights which save businesses money on maintenance and electricity costs.

To be successful in this contest you will need to provide a design and pictures for the pages listed below.

We are using the platform velbrin.com.au and you can see the attached template which everything will be loaded into so we just need HTML files which we can upload and we can do everything else from Velbrin.

The final design should be strong and clean and use the colours and textures in the attached business card file.

Detailed requirements:

Please see attached screenshot of the website template, all we need is a fantastic graphic design and improvement/ incorporation of our logo for the following pages
Page Headings:
1. Home
About Us, Contact Us, snapshot of and link to Blog

Each of the below pages will have several paragraphs of text followed by a list of suitable products which is generated from our product catalogue.

2. Car Park Lighting
3. Educational Lighting
4. Hospitality Lighting
5. Office & Shop Lighting
6. Warehouse Lighting

Some of the website we have seen which are similar in nature are:
http://www.quorvanlamps.com.au/
http://www.tibrox.com/
http://www.gandowlumen.net/commercial-led
but we really want a modern, eye catching and memorable design

Some of the designs built on Velbrin that we like are:

http://www.pemberhollow.com.au/
http://www.marwickgoods.com.au/
http://www.kelmorabay.com.au/

I've also uploaded a couple of photos that we love. We'd like something similar for each industry.

Target Market(s)

Company Owners, Maintenance & Facilities Managers, Electrical Contractors

Industry/Entity Type

Electrical

Coding

Coded - Design and coding required

Number of Pages Required

5+ page

Font styles to use
Sans Serif

Colors
33a6d7
ec1f27

Requirements
Must have
• -Must scale to mobile
• -HTML coded files need to be provided (HTML Bootstrap)
Nice to have
• -Prefer incorporation of our logo into header bar
• -Design of 2-3 advertising banners which can be displayed on the home page
• -Prominent call to action button towards top of page 'Get a quote' or similar
• -Grid based design HTML Bootstrap

```html
<!DOCTYPE html>
<html lang="en">
<head>
<meta charset="utf-8">
<title>Harlow Keane Lighting</title>
<link href="https://fonts.googleapis.com/css2?family=Raleway:wght@400;500;600;700;800&family=Open+Sans:wght@400;600&display=swap" rel="stylesheet">
<style>
:root{
  --blue:#33a6d7;
  --blue-dark:#1d7fb0;
  --red:#ec1f27;
  --ink:#2b2f33;
  --muted:#6a7076;
  --rule:#e3e6e8;
  --topbar:#1b1e21;
  --footer:#222629;
  --footer-deep:#17191b;
  --white:#ffffff;
}
*{box-sizing:border-box;margin:0;padding:0}
html,body{width:714px;height:1200px;overflow:hidden;background:var(--white)}
body{font-family:"Open Sans",Arial,sans-serif;color:var(--ink);font-size:7px;line-height:1.45;position:relative}
h1,h2,h3,h4,.nav a,.btn{font-family:"Raleway",Arial,sans-serif}

/* top bar */
.topbar{height:22px;background:var(--topbar);display:flex;align-items:center;justify-content:space-between;padding:0 32px}
.lang{color:#cfd3d6;font-size:7px;display:flex;align-items:center;gap:4px}
.lang svg{width:6px;height:6px}
.socials{display:flex;gap:5px}
.socials span{width:13px;height:13px;border-radius:50%;background:var(--blue);display:block}

/* hero */
.hero{position:relative;height:280px;overflow:hidden}
.hero-photo{position:absolute;inset:0;background:
  radial-gradient(ellipse 40% 45% at 22% 70%,rgba(255,255,230,.55),transparent 70%),
  radial-gradient(ellipse 35% 40% at 78% 68%,rgba(255,250,220,.5),transparent 70%),
  linear-gradient(180deg,#1c2733 0%,#2d4152 45%,#3c5a3a 78%,#2f4a24 100%)}
.header{position:absolute;top:0;left:0;right:0;height:38px;display:flex;align-items:center;justify-content:space-between;padding:0 32px;background:rgba(0,0,0,.35)}
.brand{display:flex;align-items:center;gap:6px;color:var(--white);font-family:"Raleway",Arial,sans-serif;font-weight:700;font-size:11px;letter-spacing:.3px}
.brand i{width:12px;height:12px;background:var(--red);display:block}
.nav{display:flex;align-items:center;gap:0;height:38px}
.nav a{color:var(--white);text-decoration:none;font-size:7.5px;font-weight:700;letter-spacing:.6px;padding:0 13px;height:38px;display:flex;align-items:center}
.nav a.active{background:var(--blue)}
.nav svg{width:9px;height:9px;margin-left:8px}
.hero-copy{position:absolute;top:112px;left:0;right:0;text-align:center}
.hero-copy h1{font-size:46px;font-weight:800;letter-spacing:2px;color:var(--blue);text-shadow:0 0 14px rgba(51,166,215,.7)}
.hero-copy p{font-family:"Raleway",Arial,sans-serif;font-weight:700;color:var(--white);font-size:11.5px;letter-spacing:.6px;margin-top:6px}
.btn-outline{display:inline-block;margin-top:14px;border:2px solid var(--white);color:var(--white);font-family:"Raleway",Arial,sans-serif;font-weight:700;font-size:10px;letter-spacing:.6px;padding:7px 22px;background:rgba(0,0,0,.35)}
.arrow{position:absolute;top:130px;width:16px;height:16px;border-radius:50%;background:rgba(255,255,255,.85);display:flex;align-items:center;justify-content:center}
.arrow svg{width:7px;height:7px}
.arrow.prev{left:10px}.arrow.next{right:10px}

/* sections */
.section{padding:0 32px}
.section-title{font-size:15px;font-weight:800;color:var(--blue);letter-spacing:.4px}
.title-row{display:flex;justify-content:space-between;align-items:center;border-bottom:1px solid var(--rule);padding-bottom:4px;margin-bottom:10px}
.pager{display:flex;gap:3px}
.pager span{width:10px;height:10px;border:1px solid var(--red);display:flex;align-items:center;justify-content:center}
.pager svg{width:5px;height:5px}

/* about */
.about{padding-top:18px;height:258px}
.about-grid{display:flex;gap:24px;margin-top:6px}
.about-text{flex:1}
.about-text h3{font-size:9px;font-weight:700;color:var(--muted);margin:4px 0 10px}
.about-text p{color:var(--muted);margin-bottom:8px}
.about-text ul{list-style:none;color:var(--muted);margin-bottom:10px}
.about-text li{padding-left:9px;position:relative}
.about-text li::before{content:"";position:absolute;left:2px;top:4px;width:3px;height:3px;border-radius:50%;background:var(--muted)}
.more{color:var(--red);font-family:"Raleway",Arial,sans-serif;font-weight:800;font-size:8.5px}
.video{width:300px;height:165px;background:linear-gradient(135deg,#2a3138,#3f4a53 50%,#23292e);position:relative;margin-top:-14px}
.video .play{position:absolute;left:50%;top:50%;width:34px;height:34px;margin:-17px 0 0 -17px}

/* products */
.products{height:246px}
.cards{display:flex;gap:12px}
.card{width:153px}
.card .photo{height:72px}
.card h4{font-size:9px;font-weight:800;color:var(--ink);margin:7px 0 3px;letter-spacing:.2px}
.card p{color:var(--muted);font-size:6.5px;margin-bottom:7px}
.btn{display:inline-block;background:var(--blue);color:var(--white);font-weight:700;font-size:6.5px;letter-spacing:.5px;padding:5px 9px}

/* blog */
.blog{height:238px}
.posts{display:flex;gap:14px}
.post{width:207px}
.post .photo{height:98px}
.post h4{font-size:9px;font-weight:800;margin:8px 0 4px}
.meta{display:flex;gap:10px;color:var(--muted);font-size:6px;margin-bottom:5px}
.meta span{display:flex;align-items:center;gap:3px}
.meta svg{width:6px;height:6px}
.post p{color:var(--muted);font-size:6.5px}

/* footer */
.footer{position:absolute;left:0;right:0;top:1040px;height:138px;background:var(--footer);padding:16px 32px 0;display:flex;gap:22px;color:#b8bec3}
.footer h4{color:var(--white);font-size:10px;font-weight:800;letter-spacing:.4px;margin-bottom:8px}
.col-company{width:95px}
.col-company li{list-style:none;font-size:7px;line-height:1.8}
.col-testimonials{width:190px}
.col-testimonials p{font-size:6.5px;margin-bottom:6px}
.col-testimonials b{color:var(--white);font-weight:600}
.col-contact{width:140px}
.contact-line{display:flex;align-items:center;gap:5px;font-size:6.5px;margin-bottom:6px}
.contact-line svg{width:8px;height:8px;flex:none}
.col-news{flex:1}
.field{height:17px;background:var(--white);margin-bottom:6px}
.subscribe{display:inline-block;background:var(--blue);color:var(--white);font-family:"Raleway",Arial,sans-serif;font-weight:700;font-size:7px;padding:5px 12px;letter-spacing:.4px}
.copyright{position:absolute;left:0;right:0;top:1178px;height:22px;background:var(--footer-deep);color:#8f969b;font-size:6.5px;display:flex;align-items:center;justify-content:center}
</style>
</head>
<body>

<div class="topbar">
  <div class="lang">English
    <svg viewBox="0 0 10 10"><path d="M1 3l4 4 4-4" fill="none" stroke="#cfd3d6" stroke-width="1.6"/></svg>
  </div>
  <div class="socials"><span></span><span></span><span></span></div>
</div>

<section class="hero">
  <div class="hero-photo" role="img" aria-label="Photograph of LED light bulbs glowing on a lawn at dusk"></div>
  <header class="header">
    <div class="brand"><i></i>Harlow Keane</div>
    <nav class="nav">
      <a class="active">HOME</a><a>ABOUT US</a><a>PRODUCTS</a><a>BLOG</a><a>CONTACT US</a>
      <svg viewBox="0 0 10 10"><circle cx="4.2" cy="4.2" r="3" fill="none" stroke="#fff" stroke-width="1.3"/><path d="M6.4 6.4l2.8 2.8" stroke="#fff" stroke-width="1.4"/></svg>
    </nav>
  </header>
  <div class="hero-copy">
    <h1>LED LIGHTS</h1>
    <p>SAVE BUSINESSES MONEY ON MAINTENANCE AND ELECTRICITY COSTS</p>
    <span class="btn-outline">CLICK HERE TO SEE MORE</span>
  </div>
  <span class="arrow prev"><svg viewBox="0 0 10 10"><path d="M7 1L3 5l4 4" fill="none" stroke="#333" stroke-width="2"/></svg></span>
  <span class="arrow next"><svg viewBox="0 0 10 10"><path d="M3 1l4 4-4 4" fill="none" stroke="#333" stroke-width="2"/></svg></span>
</section>

<section class="section about">
  <h2 class="section-title">ABOUT US</h2>
  <div class="about-grid">
    <div class="about-text">
      <h3>HARLOW KEANE BUSINESS SOLUTIONS</h3>
      <p>Retrofitting lighting in a commercial or industrial premises is a great way to save money on energy costs and maintenance, create a safer work environment and reduce the cost of running a business.</p>
      <p>We invest in your success by providing you with:</p>
      <ul>
        <li>The best range of energy saving commercial lighting</li>
        <li>High quality products from reputable makers that meet Australian standards</li>
        <li>Guidance to ensure you choose the right product for the right application</li>
      </ul>
      <span class="more">KNOW MORE &raquo;</span>
    </div>
    <div class="video" role="img" aria-label="Video still of a lit commercial interior">
      <svg class="play" viewBox="0 0 34 34"><circle cx="17" cy="17" r="16" fill="#ec1f27"/><path d="M13 10l11 7-11 7z" fill="#fff"/></svg>
    </div>
  </div>
</section>

<section class="section products">
  <div class="title-row">
    <h2 class="section-title">OUR PRODUCTS</h2>
    <div class="pager">
      <span><svg viewBox="0 0 10 10"><path d="M7 1L3 5l4 4" fill="none" stroke="#ec1f27" stroke-width="2"/></svg></span>
      <span><svg viewBox="0 0 10 10"><path d="M3 1l4 4-4 4" fill="none" stroke="#ec1f27" stroke-width="2"/></svg></span>
    </div>
  </div>
  <div class="cards">
    <article class="card">
      <div class="photo" role="img" aria-label="Car park lit by overhead LED fittings" style="background:linear-gradient(180deg,#c9d2d8,#7b8791)"></div>
      <h4>CAR PARK LIGHTING</h4>
      <p>Lorem ipsum is simply dummy text of the printing and typesetting industry.</p>
      <span class="btn">VIEW DETAILS</span>
    </article>
    <article class="card">
      <div class="photo" role="img" aria-label="Hotel lobby with warm ceiling lights" style="background:linear-gradient(180deg,#d7b98a,#7a5a3a)"></div>
      <h4>HOSPITALITY LIGHTING</h4>
      <p>Lorem ipsum is simply dummy text of the printing and typesetting industry.</p>
      <span class="btn">VIEW DETAILS</span>
    </article>
    <article class="card">
      <div class="photo" role="img" aria-label="Open plan office with panel lights" style="background:linear-gradient(180deg,#e6ecef,#9aa9b3)"></div>
      <h4>OFFICE LIGHTING</h4>
      <p>Lorem ipsum is simply dummy text of the printing and typesetting industry.</p>
      <span class="btn">VIEW DETAILS</span>
    </article>
    <article class="card">
      <div class="photo" role="img" aria-label="Bright school hall with yellow accents" style="background:linear-gradient(180deg,#f3e6a0,#c9a43b)"></div>
      <h4>EDUCATIONAL LIGHTING</h4>
      <p>Lorem ipsum is simply dummy text of the printing and typesetting industry.</p>
      <span class="btn">VIEW DETAILS</span>
    </article>
  </div>
</section>

<section class="section blog">
  <div class="title-row">
    <h2 class="section-title">OUR BLOG</h2>
    <div class="pager">
      <span><svg viewBox="0 0 10 10"><path d="M7 1L3 5l4 4" fill="none" stroke="#ec1f27" stroke-width="2"/></svg></span>
      <span><svg viewBox="0 0 10 10"><path d="M3 1l4 4-4 4" fill="none" stroke="#ec1f27" stroke-width="2"/></svg></span>
    </div>
  </div>
  <div class="posts">
    <article class="post">
      <div class="photo" role="img" aria-label="Building facade glowing with blue light at night" style="background:linear-gradient(160deg,#1b3f7a,#4e8fd6 55%,#1a2a4a)"></div>
      <h4>CONTRARY TO POPULAR BELIEF</h4>
      <div class="meta"><span><svg viewBox="0 0 10 10"><rect x="1" y="2" width="8" height="7" fill="none" stroke="#6a7076"/></svg>March 12</span><span><svg viewBox="0 0 10 10"><path d="M1 2h8v5H4L2 9V7H1z" fill="none" stroke="#6a7076"/></svg>4 comments</span></div>
      <p>Sed ut perspiciatis unde omnis iste natus error sit voluptatem accusantium doloremque laudantium, totam rem aperiam, eaque ipsa quae ab illo inventore veritatis et quasi architecto beatae vitae dicta sunt explicabo.</p>
    </article>
    <article class="post">
      <div class="photo" role="img" aria-label="Hand holding a glowing light bulb" style="background:linear-gradient(180deg,#efe9dc,#b8aa90)"></div>
      <h4>CONTRARY TO POPULAR BELIEF</h4>
      <div class="meta"><span><svg viewBox="0 0 10 10"><rect x="1" y="2" width="8" height="7" fill="none" stroke="#6a7076"/></svg>March 09</span><span><svg viewBox="0 0 10 10"><path d="M1 2h8v5H4L2 9V7H1z" fill="none" stroke="#6a7076"/></svg>2 comments</span></div>
      <p>Sed ut perspiciatis unde omnis iste natus error sit voluptatem accusantium doloremque laudantium, totam rem aperiam, eaque ipsa quae ab illo inventore veritatis et quasi architecto beatae vitae dicta sunt explicabo.</p>
    </article>
    <article class="post">
      <div class="photo" role="img" aria-label="Digital energy meter display in the dark" style="background:linear-gradient(180deg,#2a2a2c,#5b1a1a 60%,#1c1c1e)"></div>
      <h4>CONTRARY TO POPULAR BELIEF</h4>
      <div class="meta"><span><svg viewBox="0 0 10 10"><rect x="1" y="2" width="8" height="7" fill="none" stroke="#6a7076"/></svg>March 04</span><span><svg viewBox="0 0 10 10"><path d="M1 2h8v5H4L2 9V7H1z" fill="none" stroke="#6a7076"/></svg>6 comments</span></div>
      <p>Sed ut perspiciatis unde omnis iste natus error sit voluptatem accusantium doloremque laudantium, totam rem aperiam, eaque ipsa quae ab illo inventore veritatis et quasi architecto beatae vitae dicta sunt explicabo.</p>
    </article>
  </div>
</section>

<footer class="footer">
  <div class="col-company">
    <h4>COMPANY</h4>
    <ul><li>Home</li><li>About Us</li><li>Products</li><li>Blog</li><li>Contact Us</li></ul>
  </div>
  <div class="col-testimonials">
    <h4>TESTIMONIALS</h4>
    <p>"The new LED fittings cut our power bill within months and the team made the whole changeover easy." <b>&ndash; Site Manager</b></p>
    <p>"Quick quotes, clear advice and quality lights. Our car park has never looked better." <b>&ndash; Facilities Lead</b></p>
  </div>
  <div class="col-contact">
    <h4>CONTACT US</h4>
    <div class="contact-line"><svg viewBox="0 0 10 10"><path d="M5 9.5S1.5 5.8 1.5 3.8a3.5 3.5 0 017 0C8.5 5.8 5 9.5 5 9.5z" fill="#33a6d7"/><circle cx="5" cy="3.8" r="1.2" fill="#222629"/></svg>12 Quarry Lane, Brisbane QLD</div>
    <div class="contact-line"><svg viewBox="0 0 10 10"><path d="M2 1h2l1 2.5-1.3 1a5 5 0 002 2l1-1.3L9 6.2v2L8 9C4 9 1 6 1 2z" fill="#33a6d7"/></svg>(07) 5550 1234</div>
    <div class="contact-line"><svg viewBox="0 0 10 10"><path d="M2 1h2l1 2.5-1.3 1a5 5 0 002 2l1-1.3L9 6.2v2L8 9C4 9 1 6 1 2z" fill="#33a6d7"/></svg>(07) 5550 1235</div>
    <div class="contact-line"><svg viewBox="0 0 10 10"><rect x="1" y="2" width="8" height="6" fill="#33a6d7"/><path d="M1 2l4 3.5L9 2" fill="none" stroke="#222629" stroke-width=".8"/></svg>info@harlowkeane.com.au</div>
  </div>
  <div class="col-news">
    <h4>NEWS LETTER</h4>
    <div class="field"></div>
    <span class="subscribe">SUBSCRIBE</span>
  </div>
</footer>
<div class="copyright">All Copy Rights Reserved</div>

</body>
</html>
```